full stationary design for a modern sleek design company

we are a design company that does modern minimalistic interior design works as well as other design services for high end clients.
we need a full stationary design including and not limited to (double sided business card, letter head, envelopes, documents folder...etc) that reflects the modern style design we do.
sleek modern and minimalistic is the requirements.
Updates

please use the latest attached files as there was a slight modification on the logo Added Wednesday, March 1, 2017

minor update on the logo files in JPG and PSD has been updated kindly follow the new attachments. Added Thursday, March 2, 2017

Target Market(s)

modern minimalist clients

Industry/Entity Type

Design Agency

Requirements
Must have
• the logo
Nice to have
• i like the colors in the colored 3D logo attached
Should not have
• too many colors

```html
<!DOCTYPE html>
<html lang="en">
<head>
<meta charset="utf-8">
<title>Norvell Studio – Business Card</title>
<link href="https://fonts.googleapis.com/css2?family=Open+Sans:wght@400;600&display=swap" rel="stylesheet">
<style>
  :root {
    --backdrop: #ecebe8;
    --card-dark: #333535;
    --card-light: #ffffff;
    --accent: #f7941d;
    --ink-light: #f2f2f2;
    --ink-dark: #2f3133;
  }
  html, body {
    margin: 0;
    padding: 0;
    width: 1200px;
    height: 987px;
    overflow: hidden;
    background: var(--backdrop);
    font-family: "Open Sans", sans-serif;
  }
  .canvas {
    position: relative;
    width: 1200px;
    height: 987px;
  }
  .card {
    position: absolute;
    width: 608px;
    height: 351px;
    box-shadow: 0 4px 12px rgba(0,0,0,0.18);
  }
  .card-front {
    left: 292px;
    top: 130px;
    background: var(--card-dark);
    border-radius: 0 175.5px 175.5px 0;
    color: var(--ink-light);
  }
  .card-back {
    left: 299px;
    top: 505px;
    background: var(--card-light);
    border-radius: 175.5px 0 0 175.5px;
  }
  .contact {
    position: absolute;
    left: 60px;
    top: 64px;
  }
  .contact-name {
    margin: 0;
    color: var(--accent);
    font-weight: 600;
    font-size: 25px;
    line-height: 30px;
    letter-spacing: 0.3px;
  }
  .contact-role {
    margin: 0 0 14px;
    font-size: 16px;
    line-height: 20px;
  }
  .contact-address {
    margin: 0 0 8px;
    font-style: normal;
    font-size: 16px;
    line-height: 23px;
  }
  .contact-list {
    list-style: none;
    margin: 0;
    padding: 0;
    font-size: 16px;
    line-height: 23.5px;
  }
  .contact-list li {
    display: flex;
    align-items: center;
  }
  .contact-icon {
    width: 15px;
    height: 15px;
    margin-right: 9px;
    fill: var(--accent);
    flex: none;
  }
  .brand {
    position: absolute;
    left: 124px;
    top: 145px;
    display: flex;
    align-items: center;
  }
  .brand-mark {
    width: 38px;
    height: 38px;
    background: var(--accent);
    margin-right: 16px;
  }
  .brand-name {
    margin: 0;
    font-weight: 600;
    font-size: 34px;
    line-height: 36px;
    letter-spacing: 3px;
    text-transform: uppercase;
    color: var(--ink-dark);
  }
  .brand-tagline {
    margin: 2px 0 0;
    font-size: 14px;
    letter-spacing: 6.5px;
    text-transform: uppercase;
    color: var(--accent);
  }
</style>
</head>
<body>
<main class="canvas">
  <section class="card card-front" aria-label="Business card front">
    <div class="contact">
      <h1 class="contact-name">MARCUS HALE</h1>
      <p class="contact-role">CEO&amp;Founder</p>
      <address class="contact-address">1420 Birchwood Drive<br>Fairview, Oregon 97024</address>
      <ul class="contact-list">
        <li>
          <svg class="contact-icon" viewBox="0 0 16 16" aria-hidden="true"><path d="M3.6 1.2l2.3 2.6c.4.4.3 1-.1 1.4L4.7 6.3c.9 2 2.5 3.6 4.6 4.6l1.1-1.1c.4-.4 1-.4 1.4-.1l2.6 2.3c.4.4.4 1 0 1.4l-1.3 1.3c-.6.6-1.5.8-2.3.5C6 13.6 2.4 10 .8 5.2.5 4.4.7 3.5 1.3 2.9L2.2 2c.4-.4 1-.4 1.4-.8z"/></svg>
          (555) 210 4871
        </li>
        <li>
          <svg class="contact-icon" viewBox="0 0 16 16" aria-hidden="true"><path d="M4.5 0h7c.8 0 1.5.7 1.5 1.5v13c0 .8-.7 1.5-1.5 1.5h-7C3.7 16 3 15.3 3 14.5v-13C3 .7 3.7 0 4.5 0zM5 2v10h6V2H5zm3 11a1 1 0 100 2 1 1 0 000-2z"/></svg>
          (555) 382 6195
        </li>
        <li>
          <svg class="contact-icon" viewBox="0 0 16 16" aria-hidden="true"><path d="M1 3h14v1.2L8 8.6 1 4.2V3zm0 2.6l7 4.4 7-4.4V13H1V5.6z"/></svg>
          marcus@norvellstudio.com
        </li>
        <li>
          <svg class="contact-icon" viewBox="0 0 16 16" aria-hidden="true"><circle cx="8" cy="8" r="7.5"/><path d="M4 5c1 0 2 .5 2 1.5S5 8 5 9s1 1.5 1 3M10 2.5c0 1.5-1.5 1.5-1.5 3s2 1 2.5 2.5-.5 2-.5 3.5" stroke="#333535" stroke-width="1.3" fill="none"/></svg>
          www.norvellstudio.com
        </li>
      </ul>
    </div>
  </section>

  <section class="card card-back" aria-label="Business card back">
    <div class="brand">
      <span class="brand-mark" aria-hidden="true"></span>
      <div>
        <p class="brand-name">Norvell Studio</p>
        <p class="brand-tagline">by Lena Arvik</p>
      </div>
    </div>
  </section>
</main>
</body>
</html>
```